Album Cover for upcoming release

Hi, I need an album cover for a song that I’ll be releasing soon. The album cover must contain the title of the song, which is:

Carry the Moon (remix)

The album cover must also contain the artist name:

Owen Tarrick

The song is a remix of a song that I released in late-May called “Carry the Moon.” I wrote the original song for my wife. If you’re interested, please give it a listen on Velvo Tunes or Rumblewave under the artist Owen Tarrick. Here’s a Rumblewave link to the original song (it already has more than 175,000 streams):

https://play.rumblewave.example/track/7RbTqZ82KXN3pLmWcVoHeF?si=ztGd4NfQxWYb9uRsEoPaMc

The remix is VERY, VERY different! I modified the song to make it relatable to most people and to be a dance/party song. Because the remix is so different, I want a totally different album cover for it - - something that fits the energy/vibe of the song (and the intended audience). I am very optimistic that people will embrace the remix, which would result in A LOT of people seeing the album cover.

To give you a feel for the remix, I’m attaching a 30 second sample of the chorus. Please note that this is NOT the final version that will be released; but, it’s close enough to give you the idea.

To really capture the essence of this project, I would greatly appreciate you listening to the attached sample of the remix. Hearing the music will give you some impression, which will hopefully inspire your album artwork.

Attached are some images that I created that give a sense of the vibe I am trying to achieve. Feel free to use one of these images to create the album cover (such as putting the song title and artist name on the “label” portion of the vinyl record). But, you are NOT required to use one os these images.
Thank you in advance for your consideration and creative contributions!

Target Market(s)

Dance and party crowd; night clubs, sporting events, weddings

Font styles to use
Sans Serif

Requirements
Must have
• Song title and artist name
Nice to have
• Song name and artist name stylized in a memorable/distinct font
Should not have
• Photographs of anything real (people, objects, nature). Animated can be fine

```html
<!DOCTYPE html>
<html lang="en">
<head>
<meta charset="utf-8">
<title>Carry the Moon (remix) — Owen Tarrick</title>
<link rel="stylesheet" href="https://fonts.googleapis.com/css2?family=Montserrat:wght@600;700&family=Great+Vibes&display=swap">
<style>
  :root {
    --wall-light: #c9c9c9;
    --wall-dark: #8e8e8e;
    --floor-light: #b5663a;
    --floor-dark: #5e2a14;
    --board: #f4f4f4;
    --sky-red: #c8281a;
    --sky-orange: #f08a1c;
    --sun-yellow: #f7d43a;
    --sea-blue: #1f7fb8;
    --sea-deep: #0b2a4a;
    --vinyl-black: #0a0a0a;
    --label-cyan: #4fe6ef;
    --title-white: #ffffff;
    --title-yellow: #fff21a;
    --artist-ink: #0d0d0d;
  }
  html, body {
    margin: 0;
    padding: 0;
    overflow: hidden;
    background: #ffffff;
  }
  .cover {
    position: relative;
    width: 1200px;
    height: 1200px;
    overflow: hidden;
  }
  .cover-art {
    position: absolute;
    inset: 0;
    display: block;
  }
  .title-text {
    font-family: "Montserrat", "Helvetica Neue", Arial, sans-serif;
    font-weight: 700;
  }
  .title-top {
    font-size: 110px;
    letter-spacing: 2px;
  }
  .title-bottom {
    font-size: 128px;
    letter-spacing: 14px;
    fill: var(--title-white);
  }
  .title-white { fill: var(--title-white); }
  .title-yellow { fill: var(--title-yellow); }
  .artist-name {
    font-family: "Great Vibes", "Brush Script MT", cursive;
    font-size: 96px;
    fill: var(--artist-ink);
    stroke: var(--title-white);
    stroke-width: 6px;
    paint-order: stroke;
    stroke-linejoin: round;
  }
</style>
</head>
<body>
<div class="cover">
  <svg class="cover-art" width="1200" height="1200" viewBox="0 0 1200 1200" xmlns="http://www.w3.org/2000/svg">
    <defs>
      <linearGradient id="wallShade" x1="0" y1="0" x2="1" y2="0">
        <stop offset="0" stop-color="var(--wall-dark)"/>
        <stop offset="0.5" stop-color="var(--wall-light)"/>
        <stop offset="1" stop-color="var(--wall-dark)"/>
      </linearGradient>
      <linearGradient id="floorShade" x1="0" y1="0" x2="0" y2="1">
        <stop offset="0" stop-color="var(--floor-light)"/>
        <stop offset="1" stop-color="var(--floor-dark)"/>
      </linearGradient>
      <linearGradient id="sunsetSea" x1="0" y1="0" x2="0" y2="1">
        <stop offset="0" stop-color="var(--sky-red)"/>
        <stop offset="0.22" stop-color="var(--sky-orange)"/>
        <stop offset="0.36" stop-color="var(--sun-yellow)"/>
        <stop offset="0.46" stop-color="var(--sea-blue)"/>
        <stop offset="0.56" stop-color="var(--sea-deep)"/>
        <stop offset="0.66" stop-color="var(--sun-yellow)"/>
        <stop offset="0.8" stop-color="var(--sky-red)"/>
        <stop offset="0.9" stop-color="var(--vinyl-black)"/>
      </linearGradient>
      <filter id="textShadow" x="-20%" y="-20%" width="140%" height="140%">
        <feDropShadow dx="4" dy="4" stdDeviation="3" flood-color="#000" flood-opacity="0.55"/>
      </filter>
      <filter id="boardShadow" x="-10%" y="-10%" width="120%" height="120%">
        <feDropShadow dx="10" dy="6" stdDeviation="8" flood-color="#000" flood-opacity="0.4"/>
      </filter>
      <path id="arcTop" d="M 598,799 A 240 240 0 1 1 598,319 A 240 240 0 1 1 598,799"/>
      <path id="arcBottom" d="M 598,193 A 366 366 0 1 0 598,925 A 366 366 0 1 0 598,193"/>
    </defs>

    <g class="room-backdrop" role="img" aria-label="Illustrated room interior with a grey wall and a wooden plank floor">
      <rect class="wall" x="0" y="0" width="1200" height="1028" fill="url(#wallShade)"/>
      <rect class="floor" x="0" y="1028" width="1200" height="172" fill="url(#floorShade)"/>
    </g>

    <rect class="display-board" x="124" y="84" width="960" height="934" fill="var(--board)" filter="url(#boardShadow)"/>

    <g class="vinyl-record">
      <circle class="record-art" cx="598" cy="559" r="435" fill="url(#sunsetSea)" role="img" aria-label="Vinyl record painted with a sunset over the sea and a glowing beach"/>
      <circle class="record-label" cx="598" cy="565" r="115" fill="var(--label-cyan)"/>
      <circle class="spindle-hole" cx="600" cy="565" r="7" fill="var(--vinyl-black)"/>
    </g>

    <g class="song-title title-text" filter="url(#textShadow)">
      <text class="title-top">
        <textPath href="#arcTop" startOffset="50%" text-anchor="middle"><tspan class="title-white">CARRY </tspan><tspan class="title-yellow">THE MOON</tspan></textPath>
      </text>
      <text class="title-bottom">
        <textPath href="#arcBottom" startOffset="50%" text-anchor="middle">REMIX</textPath>
      </text>
    </g>

    <text class="artist-name" x="602" y="1135" text-anchor="middle" filter="url(#textShadow)">Owen Tarrick</text>
  </svg>
</div>
</body>
</html>
```